Rovelux

Hi everyone!

Looks like our project is more sophisticated than we expected. So good news - we increased the budget! and one of you will sure get the prize - no money back for us!

We are a young Russian company that specializes in in-taxi entertainment. We believe that our key strength is great attention to user experience. We've devoted much effort to improve ergonomics of our devices - tablet PCs that we install in the taxis. And yes, we enjoy to simplify things!

Now we need the most basic things - a logo and some staff for client meetings (primarily advertisers and ad agencies).

As for logo - we already have one engraved on the prototypes of our device (see attached file). This is one of the ideas (still far from perfect) - what we appreciate in it is minimalistic yet stylish approach.

As for "take it to the meeting stuff" we want to start with name card, pen and notepad (A4) that we will leave in clients's office, also as a reminder. Shall your have more smart ideas - always welcome!

As for logo and name cards - we would like to make an image of serious but modern company. Our design should communicate creativity and reliability. We believe that "to understand is to simplify" - minimalistic design is the most difficult one. Its better to work hard on fonts and arrangement, than put 10 variegated images.

SO THE TASK IS TO DESIGN:
- a logo
- a name card
- a note pad (great example in attachment)
- a pen

Shall you have more questions - please ask in comments.

We look forward to meeting like-minded fellows here!
Updates

Target Market(s)

Out target are:

- advertiser
- advertising agencies
- taxi passenger

Industry/Entity Type

It Company

Requirements
Must have
• font should be chosen very carefully
Nice to have
• classic minimalistic plain text only but very stylish name card is a dream of one of our co-founders:)
Should not have
• we do not want to have taxi-like colors and chess-boards. We are closer to "innovation", "entertainment", and "user experience", rather than "taxi".

```html
<!DOCTYPE html>
<html lang="en">
<head>
<meta charset="utf-8">
<title>Rovelux — logo and name card options</title>
<link rel="stylesheet" href="https://fonts.googleapis.com/css2?family=Questrial&display=swap">
<style>
  :root {
    --ink: #231f20;
    --accent: #f7941d;
    --paper: #ffffff;
    --stage: #d5dde3;
    --rule: #a7a9ac;
    --muted: #9a9a9a;
  }
  * { box-sizing: border-box; margin: 0; padding: 0; }
  html, body { width: 1200px; height: 1000px; overflow: hidden; }
  body {
    position: relative;
    background: var(--paper);
    font-family: "Questrial", "Helvetica Neue", Arial, sans-serif;
    color: var(--ink);
  }
  .logo-strip { position: absolute; inset: 0 0 auto 0; height: 233px; background: var(--paper); }
  .stage { position: absolute; left: 0; right: 0; top: 233px; bottom: 0; background: var(--stage); }

  .mark { position: absolute; display: flex; flex-direction: column; line-height: 1; }
  .mark-name { display: flex; align-items: center; letter-spacing: -0.02em; }
  .mark-dot { display: inline-block; border-radius: 50%; background: var(--accent); }
  .mark-tag { align-self: flex-end; letter-spacing: 0.01em; }

  .mark--large .mark-name { font-size: 80px; line-height: 0.9; gap: 10px; }
  .mark--large .mark-dot { width: 14px; height: 14px; }
  .mark--large .mark-tag { font-size: 25px; line-height: 1; margin-top: 2px; }
  .mark--reversed { color: var(--paper); }

  .reverse-panel { position: absolute; left: 633px; top: 59px; width: 433px; height: 124px; background: var(--ink); }

  .option-number { position: absolute; font-size: 24px; color: var(--ink); }

  .card {
    position: absolute; width: 464px; height: 257px; background: var(--paper);
    box-shadow: 0 2px 6px rgba(0,0,0,0.18);
  }
  .mark--card .mark-name { font-size: 50px; gap: 6px; }
  .mark--card .mark-dot { width: 8px; height: 8px; }
  .mark--card .mark-tag { font-size: 15px; margin-top: 2px; }

  .contacts { position: absolute; font-size: 14px; line-height: 18px; letter-spacing: 0.02em; color: var(--ink); white-space: nowrap; }
  .contacts--centered { left: 0; right: 0; text-align: center; }
  .contacts .sep { color: var(--muted); padding: 0 4px; }
  .contacts--listed .sep { color: var(--accent); }
  .contacts--listed .bullet { color: var(--accent); padding-right: 6px; }

  .card-rule { position: absolute; height: 1px; background: var(--rule); }
</style>
</head>
<body>
  <section class="logo-strip">
    <div class="mark mark--large" style="left:135px; top:74px;">
      <div class="mark-name">Rovelux <span class="mark-dot"></span></div>
      <div class="mark-tag">taxi entertainment</div>
    </div>
    <div class="reverse-panel"></div>
    <div class="mark mark--large mark--reversed" style="left:652px; top:74px;">
      <div class="mark-name">Rovelux <span class="mark-dot"></span></div>
      <div class="mark-tag">taxi entertainment</div>
    </div>
  </section>

  <section class="stage"></section>

  <span class="option-number" style="left:48px; top:330px;">1</span>
  <article class="card" style="left:84px; top:325px;">
    <div class="mark mark--card" style="left:116px; top:78px;">
      <div class="mark-name">Rovelux <span class="mark-dot"></span></div>
      <div class="mark-tag">taxi entertainment</div>
    </div>
    <p class="contacts contacts--centered" style="top:188px;">
      Moscow, Ulitsa Sadovaya, 12<br>
      tel: +495 210 47 385<span class="sep">•</span>mob: +495 318 260 574<br>
      rovelux.com<span class="sep">•</span>e-mail: rovelux@mailbox.com
    </p>
  </article>

  <span class="option-number" style="left:593px; top:330px;">2</span>
  <article class="card" style="left:644px; top:325px;">
    <div class="mark mark--card" style="right:30px; top:24px;">
      <div class="mark-name">Rovelux <span class="mark-dot"></span></div>
      <div class="mark-tag">taxi entertainment</div>
    </div>
    <p class="contacts contacts--listed" style="left:16px; top:190px;">
      <span class="bullet">•</span>Moscow, Ulitsa Sadovaya, 12<br>
      <span class="bullet">•</span>tel: +495 210 47 385<span class="sep">•</span>mob: +495 318 260 574<br>
      <span class="bullet">•</span>rovelux.com<span class="sep">•</span>e-mail: rovelux@mailbox.com
    </p>
  </article>

  <span class="option-number" style="left:48px; top:662px;">3</span>
  <article class="card" style="left:84px; top:665px;">
    <div class="mark mark--card" style="left:116px; top:86px;">
      <div class="mark-name">Rovelux <span class="mark-dot"></span></div>
      <div class="mark-tag">taxi entertainment</div>
    </div>
    <div class="card-rule" style="left:116px; width:232px; top:187px;"></div>
    <p class="contacts contacts--centered" style="top:193px;">
      Moscow, Ulitsa Sadovaya, 12<br>
      tel: +495 210 47 385<span class="sep">•</span>mob: +495 318 260 574<br>
      rovelux.com<span class="sep">•</span>e-mail: rovelux@mailbox.com
    </p>
  </article>

  <span class="option-number" style="left:593px; top:662px;">4</span>
  <article class="card" style="left:644px; top:665px;">
    <div class="mark mark--card" style="left:18px; top:100px;">
      <div class="mark-name">Rovelux <span class="mark-dot"></span></div>
      <div class="mark-tag">taxi entertainment</div>
    </div>
    <div class="card-rule" style="left:18px; width:238px; top:178px;"></div>
    <p class="contacts contacts--listed" style="left:16px; top:188px;">
      <span class="bullet">•</span>Moscow, Ulitsa Sadovaya, 12<br>
      <span class="bullet">•</span>tel: +495 210 47 385<span class="sep">•</span>mob: +495 318 260 574<br>
      <span class="bullet">•</span>rovelux.com<span class="sep">•</span>e-mail: rovelux@mailbox.com
    </p>
  </article>
</body>
</html>
```